Business Card for premium dental clinic

We are a premium dental clinic based in Brasov, Romania with more than 15 year on the market, providing quality dental treatment made by a team of more specialized dentists, working with modern equipment as a solution to beautiful and healthy teeth.

Our current logo for the clinic use 2 square with colors black and gold - dr Ternisu - studio, using family fonts Bodoni, Myriad Pro and Segoe Print.
Depending on the printing we used some gold CMYK background or gold foil picture background or a gold gradient.
We want a business card:
- eye catching business card
- distinguished business card
- premium design
- to keep the color scheme of black and gold
- to attract the customers to spent time reading the information
- modern concept

```html
<!DOCTYPE html>
<html lang="en">
<head>
<meta charset="utf-8">
<title>dr Ternisu studio – business card</title>
<link href="https://fonts.googleapis.com/css2?family=Pathway+Gothic+One&family=Lato:wght@400;700&display=swap" rel="stylesheet">
<style>
  :root{
    --ink:#070707;
    --paper:#ffffff;
    --gold:#e3a928;
    --gold-light:#f7d24e;
    --gold-deep:#c8861c;
    --name-gold:#d4882a;
    --stage:#e9e6e1;
  }
  *{box-sizing:border-box;margin:0;padding:0}
  html,body{width:1200px;height:1023px;overflow:hidden}
  body{background:var(--stage);position:relative;font-family:'Lato',sans-serif}
  .card{position:absolute;left:255px;width:690px;height:396px;overflow:hidden;
        box-shadow:0 6px 18px rgba(0,0,0,.25)}
  .card-front{top:86px;background:var(--ink)}
  .card-back{top:541px;background:var(--ink)}
  .card-art{position:absolute;inset:0}
  .brand{font-family:'Pathway Gothic One',sans-serif;font-weight:400;color:var(--ink);line-height:1;white-space:nowrap}
  .front-brand{position:absolute;left:40px;top:34px;font-size:98px}
  .front-brand-sub{position:absolute;left:94px;top:136px;font-size:62px}
  .holder{position:absolute;right:34px;text-align:right;color:var(--paper)}
  .holder-name{top:206px;font-weight:700;font-size:31px;color:var(--name-gold);letter-spacing:.5px}
  .holder-role{top:250px;font-size:15px}
  .contact{position:absolute;right:30px;display:flex;align-items:center;gap:10px;color:var(--paper);font-size:17px}
  .contact svg{width:18px;height:18px}
  .contact-phone{top:276px}
  .contact-mail{top:307px}
  .contact-web{top:338px}
  .address{position:absolute;left:33px;top:320px;color:var(--paper);font-size:17px;line-height:24px}
  .foil{position:absolute;left:0;top:0;width:350px;height:396px;
        background:radial-gradient(circle at 30% 30%,var(--gold-light),var(--gold) 55%,var(--gold-deep))}
  .logo-plate{position:absolute;left:46px;top:123px;width:304px;height:142px;background:var(--paper);
              display:flex;align-items:center;justify-content:center;overflow:hidden}
  .back-brand{font-size:84px}
  .back-brand-sub{position:absolute;left:350px;right:0;top:160px;text-align:center;font-size:84px;color:var(--paper)}
  .tagline{position:absolute;right:14px;top:332px;font-family:'Pathway Gothic One',sans-serif;font-size:50px;color:var(--paper);line-height:1;white-space:nowrap}
</style>
</head>
<body>
  <section class="card card-front">
    <svg class="card-art" viewBox="0 0 690 396" aria-hidden="true">
      <defs>
        <linearGradient id="swoosh-gold" x1="0" y1="0" x2="1" y2="0">
          <stop offset="0" stop-color="#d99a22"/>
          <stop offset=".5" stop-color="#f6cf48"/>
          <stop offset="1" stop-color="#e8b02e"/>
        </linearGradient>
      </defs>
      <path d="M0,0 H576 C530,105 470,200 385,248 C270,300 90,292 0,244 Z" fill="var(--paper)"/>
      <path d="M0,178 C70,252 260,268 378,212 C428,188 462,162 483,138 C462,176 432,206 392,228 C272,292 82,284 0,226 Z" fill="url(#swoosh-gold)" role="img" aria-label="gold foil swoosh"/>
    </svg>
    <div class="brand front-brand">dr ternisu</div>
    <div class="brand front-brand-sub">studio</div>
    <div class="holder holder-name">JOHN SMITH</div>
    <div class="holder holder-role">Managing Director</div>
    <div class="contact contact-phone">123 456 7890
      <svg viewBox="0 0 24 24"><path d="M6.6 10.8a15 15 0 0 0 6.6 6.6l2.2-2.2c.3-.3.7-.4 1-.2 1.1.4 2.3.6 3.6.6.6 0 1 .4 1 1V20c0 .6-.4 1-1 1C10.6 21 3 13.4 3 4c0-.6.4-1 1-1h3.5c.6 0 1 .4 1 1 0 1.3.2 2.5.6 3.6.1.3 0 .7-.2 1z" fill="#fff"/></svg>
    </div>
    <div class="contact contact-mail">lorem@yourwebsite.com
      <svg viewBox="0 0 24 24"><rect x="2" y="5" width="20" height="14" fill="#fff"/><path d="M2 5l10 8 10-8M2 19l8-7M22 19l-8-7" stroke="var(--ink)" stroke-width="1.6" fill="none"/></svg>
    </div>
    <div class="contact contact-web">www.yourwebsite.com
      <svg viewBox="0 0 24 24" fill="none" stroke="#fff" stroke-width="1.6"><circle cx="12" cy="12" r="9"/><ellipse cx="12" cy="12" rx="4" ry="9"/><path d="M3 12h18M5 7h14M5 17h14"/></svg>
    </div>
    <div class="address">2345 First Address Line<br>Second Address Line, 56324</div>
  </section>

  <section class="card card-back">
    <div class="foil" role="img" aria-label="crumpled gold foil texture"></div>
    <div class="logo-plate"><span class="brand back-brand">dr ternisu</span></div>
    <div class="brand back-brand-sub">studio</div>
    <div class="tagline">dental clinic</div>
  </section>
</body>
</html>
```